NimbaVault Website Homepage Design

Please provide your idea of homepage for a hosting company. This project is for DESIGN only, no coding.

It must use/combine colors used in logo, clean, modern look.

Homepage must consist of at least 4 sections (example: testimonials, services, and so on. not necesarily all of them). We would like the navigation to be horizontal, but not mandatory.

You can include a preview of services page (optional, not a must).

Number of Pages Required

1 page

Font styles to use
Sans Serif

```html
<!DOCTYPE html>
<html lang="en">
<head>
<meta charset="utf-8">
<title>NimbaVault — Web Hosting</title>
<link rel="stylesheet" href="https://fonts.googleapis.com/css2?family=Montserrat:wght@400;500;700;800&family=Roboto:wght@400;500;700&display=swap">
<style>
:root{
  --blue:#0a7ad6;
  --blue-dark:#0563b0;
  --ink:#1d1d1f;
  --text:#6b6f76;
  --grey-bar:#6d6e71;
  --grey-band:#939598;
  --soft:#f3f6fb;
  --footer:#58595b;
  --white:#ffffff;
  --line:#d9dde3;
  --star:#f5b50a;
}
*{box-sizing:border-box;margin:0;padding:0}
html,body{width:1200px;height:4047px;overflow:hidden}
body{font-family:Roboto,Arial,sans-serif;color:var(--ink);background:var(--white);position:relative}
section,header,footer,.topbar{position:absolute;left:0;width:1200px}
.abs{position:absolute}
.h-title{position:absolute;left:0;width:1200px;text-align:center;font-family:Montserrat,Arial,sans-serif;font-size:38px;color:#8a8d92;font-weight:400;letter-spacing:.5px}
.h-title b{color:var(--blue);font-weight:800}

/* top bar */
.topbar{top:0;height:35px;background:var(--grey-bar);color:var(--white);font-size:13px}
.topbar span{position:absolute;top:9px;display:flex;align-items:center;gap:6px}
.topbar u{margin-left:14px}
.social-mini{position:absolute;top:7px;width:21px;height:21px;border-radius:50%;background:#8e8f92}

/* header */
header{top:35px;height:95px;background:var(--white)}
.brand{position:absolute;left:110px;top:29px;font-family:Montserrat,Arial,sans-serif;font-weight:700;font-size:30px;color:var(--blue);letter-spacing:1px}
.nav{position:absolute;top:40px;font-size:15px;font-weight:500;color:var(--ink)}
.nav.active{color:var(--blue)}
.nav.active::before{content:"";position:absolute;left:50%;top:-12px;margin-left:-4px;border:4px solid transparent;border-bottom:6px solid var(--blue)}
.login{position:absolute;left:984px;top:30px;width:103px;height:36px;border-radius:18px;background:var(--blue);color:var(--white);font-size:15px;font-weight:500;display:flex;align-items:center;justify-content:center;gap:6px}

/* hero */
.hero{top:130px;height:592px}
.hero-photo{position:absolute;inset:0;background:linear-gradient(100deg,#0b2a55 0%,#154b8c 45%,#2a6fb6 75%,#0f3562 100%)}
.hero h1{position:absolute;left:108px;top:196px;font-family:Montserrat,Arial,sans-serif;font-weight:800;font-size:42px;color:var(--white)}
.hero p{position:absolute;left:110px;top:254px;width:420px;font-size:16px;font-weight:500;line-height:26px;color:var(--white)}
.btn-blue{position:absolute;height:50px;border-radius:25px;background:var(--blue);color:var(--white);font-weight:700;font-size:16px;display:flex;align-items:center;justify-content:center;gap:8px}

/* services */
.services{top:722px;height:712px;background:var(--soft)}
.svc{position:absolute;width:306px;height:202px;background:var(--white);box-shadow:0 2px 10px rgba(0,0,0,.05)}
.svc .ic{position:absolute;left:16px;top:-23px;width:62px;height:62px;border-radius:50%;background:var(--white);display:flex;align-items:center;justify-content:center}
.svc .bar{position:absolute;left:16px;top:51px;width:32px;height:4px;background:var(--blue)}
.svc h3{position:absolute;left:16px;top:72px;font-size:17px;font-weight:500}
.svc p{position:absolute;left:16px;top:104px;width:280px;font-size:14px;line-height:23px;color:var(--text)}

/* plans */
.plans{top:1434px;height:760px}
.plan{position:absolute;top:165px;width:230px;height:486px;border:2px solid var(--line);background:var(--white);text-align:center}
.plan .hex{position:absolute;left:82px;top:20px}
.plan h3{position:absolute;left:0;right:0;top:106px;font-size:19px;font-weight:500}
.price{position:absolute;left:0;right:0;top:138px;font-weight:500;font-size:13px}
.price b{font-size:38px;color:var(--blue);font-weight:700;vertical-align:-4px}
.setup{position:absolute;left:0;right:0;top:197px;height:29px;background:var(--grey-band);color:var(--white);font-size:13px;line-height:29px}
.plan ul{position:absolute;left:16px;top:256px;list-style:none;text-align:left;font-size:14px;color:var(--text)}
.plan li{height:29px;display:flex;align-items:center;gap:8px}
.btn-line{position:absolute;left:46px;top:422px;width:138px;height:38px;border:2px solid var(--blue);border-radius:19px;color:var(--blue);font-weight:700;font-size:15px;line-height:34px;background:var(--white)}
.plan.pro{background:var(--blue);border-color:var(--blue);color:var(--white)}
.plan.pro .price b,.plan.pro ul{color:var(--white)}
.plan.pro .btn-line{border-color:var(--white)}

/* signup band */
.signup{top:2194px;height:280px}
.signup-photo{position:absolute;inset:0;background:linear-gradient(90deg,#1a5fae 0%,#2b86da 50%,#1a5fae 100%)}
.signup h2{position:absolute;left:0;width:1200px;text-align:center;font-family:Montserrat,Arial,sans-serif;font-size:34px;color:var(--white);line-height:40px;top:53px;font-weight:400}
.signup h2 b{font-weight:800}
.pill{position:absolute;top:171px;width:189px;height:46px;border-radius:23px;font-weight:700;font-size:16px;display:flex;align-items:center;justify-content:center;gap:8px}

/* why */
.why{top:2474px;height:699px}
.why-photo{position:absolute;left:111px;top:107px;width:400px;height:468px;border-radius:10px;background:linear-gradient(160deg,#1b3f6e,#2f72b8 60%,#173860)}
.why h2{position:absolute;left:580px;top:110px;font-family:Montserrat,Arial,sans-serif;font-size:36px;color:#8a8d92;font-weight:400}
.why h2 b{color:var(--blue);font-weight:800}
.why .lead{position:absolute;left:580px;top:172px;width:500px;font-size:14px;line-height:24px;color:var(--text)}
.feat{position:absolute;width:240px}
.feat .ic{width:50px;height:50px;border-radius:50%;background:var(--soft);display:flex;align-items:center;justify-content:center}
.feat h4{margin-top:20px;font-size:17px;font-weight:500}
.feat p{margin-top:8px;font-size:13.5px;line-height:21px;color:var(--text)}

/* testimonials */
.clients{top:3173px;height:521px;background:var(--soft)}
.quote{position:absolute;top:173px;width:308px;height:189px;background:var(--white);border-top:3px solid var(--blue);border-radius:8px;box-shadow:0 3px 12px rgba(0,0,0,.05);text-align:center}
.quote::after{content:"";position:absolute;left:144px;bottom:-10px;border:10px solid transparent;border-bottom:0;border-top-color:var(--white)}
.avatar{position:absolute;left:107px;top:-50px;width:94px;height:94px;border-radius:50%;border:4px solid var(--white);background:linear-gradient(#c9a78b,#7a5b48)}
.quote p{position:absolute;left:22px;right:22px;top:72px;font-size:14px;line-height:26px;color:var(--text)}
.who{position:absolute;top:386px;width:308px;text-align:center;font-size:15px;font-weight:500}
.who small{font-size:10px;font-weight:400}
.stars{display:block;margin-top:3px;color:var(--star);font-size:12px;letter-spacing:1px}

/* footer */
footer{top:3694px;height:353px;background:var(--footer);color:var(--white)}
footer h5{position:absolute;top:62px;font-size:18px;font-weight:700}
.fitem{position:absolute;left:110px;font-size:14px;display:flex;gap:12px;line-height:20px}
.flink{position:absolute;font-size:14px}
.email{position:absolute;left:715px;top:110px;width:235px;height:44px;border-radius:22px;background:var(--white);color:#999;font-size:12px;line-height:44px;padding-left:22px}
.submit{position:absolute;left:965px;top:110px;width:122px;height:44px;border-radius:22px;background:var(--blue);font-weight:700;font-size:17px;text-align:center;line-height:44px}
.fsoc{position:absolute;top:222px;width:30px;height:30px;border-radius:50%;border:1.5px solid var(--white)}
.divider{position:absolute;left:110px;top:288px;width:977px;height:1px;background:#7a7b7e}
.copy{position:absolute;left:0;width:1200px;top:312px;text-align:center;font-size:13px}
</style>
</head>
<body>

<div class="topbar">
  <span style="left:110px"><svg width="10" height="12" viewBox="0 0 10 12"><path d="M5 0a4 4 0 0 0-4 4c0 3 4 8 4 8s4-5 4-8a4 4 0 0 0-4-4zm0 5.5A1.5 1.5 0 1 1 5 2.5a1.5 1.5 0 0 1 0 3z" fill="#fff"/></svg>My office: &nbsp;722 Lorem ipsum dolor sit amet<u>Find Other Office</u></span>
  <span style="left:660px"><svg width="11" height="11" viewBox="0 0 12 12"><path d="M2.5 0l2 3-1.3 1.3a8 8 0 0 0 4.5 4.5L9 7.5l3 2-1.5 2.5C5 12 0 7 0 1.5z" fill="#fff"/></svg>555 014 2290</span>
  <span style="left:820px"><svg width="12" height="9" viewBox="0 0 12 9"><rect width="12" height="9" fill="#fff"/><path d="M0 0l6 5 6-5" stroke="#6d6e71" fill="none"/></svg>info@nimbavault.com</span>
  <i class="social-mini" style="left:1001px"></i><i class="social-mini" style="left:1033px"></i><i class="social-mini" style="left:1065px"></i>
</div>

<header>
  <div class="brand">NIMBAVAULT</div>
  <span class="nav active" style="left:418px">Home</span>
  <span class="nav" style="left:487px">About Us</span>
  <span class="nav" style="left:577px">Services</span>
  <span class="nav" style="left:664px">Plan</span>
  <span class="nav" style="left:720px">Blog</span>
  <span class="nav" style="left:779px">Support</span>
  <span class="nav" style="left:860px">Contact</span>
  <svg class="abs" style="left:941px;top:42px" width="15" height="15" viewBox="0 0 15 15"><circle cx="6" cy="6" r="4.5" stroke="#1d1d1f" stroke-width="2" fill="none"/><path d="M9.5 9.5l4 4" stroke="#1d1d1f" stroke-width="2"/></svg>
  <div class="login"><svg width="11" height="12" viewBox="0 0 11 12"><rect y="5" width="11" height="7" rx="1" fill="#fff"/><path d="M2.5 5V3.5a3 3 0 0 1 6 0V5" stroke="#fff" stroke-width="1.6" fill="none"/></svg>Login</div>
</header>

<section class="hero">
  <div class="hero-photo" role="img" aria-label="Two engineers reviewing a laptop in a server room"></div>
  <h1>NIMBAVAULT</h1>
  <p>Lorem ipsum dolor sit amet, consectetur adipiscing elit, sed eiusmod tempor incididunt ut</p>
  <div class="btn-blue" style="left:112px;top:332px;width:183px">GET STARTED <svg width="15" height="15" viewBox="0 0 16 16"><circle cx="8" cy="8" r="8" fill="#fff"/><path d="M6.5 4.5L10 8l-3.5 3.5" stroke="#0a7ad6" stroke-width="2" fill="none"/></svg></div>
</section>

<section class="services">
  <div class="h-title" style="top:67px"><b>OUR</b> SERVICES</div>

  <div class="svc" style="left:111px;top:173px"><div class="ic"><svg width="40" height="40" viewBox="0 0 40 40" fill="none" stroke="#0a7ad6" stroke-width="1.6"><rect x="6" y="6" width="28" height="24" rx="2"/><path d="M6 12h28M10 17h20M10 22h20M16 30v5h8v-5"/></svg></div><div class="bar"></div><h3>Web Hosting</h3><p>Sed ut perspiciatis unde omnis iste natus sit voluptatem accusantium doloremque laudantium, totam aperiam,</p></div>
  <div class="svc" style="left:446px;top:173px"><div class="ic"><svg width="40" height="40" viewBox="0 0 40 40" fill="none" stroke="#0a7ad6" stroke-width="1.6"><rect x="7" y="6" width="26" height="8" rx="1"/><rect x="7" y="16" width="26" height="8" rx="1"/><rect x="7" y="26" width="26" height="8" rx="1"/><circle cx="12" cy="10" r="1"/><circle cx="12" cy="20" r="1"/><circle cx="12" cy="30" r="1"/></svg></div><div class="bar"></div><h3>Cloud Hosting</h3><p>Sed ut perspiciatis unde omnis iste natus sit voluptatem accusantium doloremque laudantium, totam aperiam,</p></div>
  <div class="svc" style="left:781px;top:173px"><div class="ic"><svg width="40" height="40" viewBox="0 0 40 40" fill="none" stroke="#0a7ad6" stroke-width="1.6"><path d="M11 16a6 6 0 0 1 2-11 8 8 0 0 1 14 2 5 5 0 0 1 2 9z"/><rect x="12" y="20" width="16" height="6" rx="1"/><rect x="12" y="28" width="16" height="6" rx="1"/></svg></div><div class="bar"></div><h3>Wordpress Hosting</h3><p>Sed ut perspiciatis unde omnis iste natus sit voluptatem accusantium doloremque laudantium, totam aperiam,</p></div>

  <div class="svc" style="left:111px;top:433px"><div class="ic"><svg width="40" height="40" viewBox="0 0 40 40" fill="none" stroke="#0a7ad6" stroke-width="1.6"><path d="M10 18a7 7 0 0 1 4-12 9 9 0 0 1 16 4 5 5 0 0 1 0 9"/><rect x="8" y="20" width="13" height="14" rx="1"/><rect x="23" y="22" width="10" height="12" rx="1"/></svg></div><div class="bar"></div><h3>VPS</h3><p>Sed ut perspiciatis unde omnis iste natus sit voluptatem accusantium doloremque laudantium, totam aperiam,</p></div>
  <div class="svc" style="left:446px;top:433px"><div class="ic"><svg width="40" height="40" viewBox="0 0 40 40" fill="none" stroke="#0a7ad6" stroke-width="1.6"><ellipse cx="20" cy="9" rx="10" ry="4"/><path d="M10 9v20c0 2 4.5 4 10 4s10-2 10-4V9M10 16c0 2 4.5 4 10 4s10-2 10-4M10 23c0 2 4.5 4 10 4s10-2 10-4"/></svg></div><div class="bar"></div><h3>Dedicated Server</h3><p>Sed ut perspiciatis unde omnis iste natus sit voluptatem accusantium doloremque laudantium, totam aperiam,</p></div>
  <div class="svc" style="left:781px;top:433px"><div class="ic"><svg width="40" height="40" viewBox="0 0 40 40" fill="none" stroke="#0a7ad6" stroke-width="1.6"><rect x="6" y="8" width="28" height="24" rx="2"/><path d="M11 14h18M11 20h18M11 26h10"/><rect x="24" y="24" width="6" height="5"/></svg></div><div class="bar"></div><h3>Shared Hosting</h3><p>Sed ut perspiciatis unde omnis iste natus sit voluptatem accusantium doloremque laudantium, totam aperiam,</p></div>
</section>

<section class="plans">
  <div class="h-title" style="top:76px">NIMBAVAULT <b>PLANS</b></div>

  <div class="plan" style="left:97px">
    <svg class="hex" width="66" height="74" viewBox="0 0 66 74"><path d="M33 0l33 18.5v37L33 74 0 55.5v-37z" fill="#0a7ad6"/><rect x="25" y="22" width="16" height="28" rx="2" stroke="#fff" stroke-width="2" fill="none"/><path d="M29 30h8M29 36h8" stroke="#fff" stroke-width="2"/></svg>
    <h3>Basic Plan</h3><div class="price">$ <b>15</b> .00/mo</div><div class="setup">Free Instant Setup</div>
    <ul><li><svg width="13" height="13" viewBox="0 0 14 14"><circle cx="7" cy="7" r="7" fill="#0a7ad6"/><path d="M4 7l2 2 4-4" stroke="#fff" stroke-width="1.8" fill="none"/></svg>Sed ut perspiciatis unde</li><li><svg width="13" height="13" viewBox="0 0 14 14"><circle cx="7" cy="7" r="7" fill="#0a7ad6"/><path d="M4 7l2 2 4-4" stroke="#fff" stroke-width="1.8" fill="none"/></svg>omnis iste natus error sit</li><li><svg width="13" height="13" viewBox="0 0 14 14"><circle cx="7" cy="7" r="7" fill="#0a7ad6"/><path d="M4 7l2 2 4-4" stroke="#fff" stroke-width="1.8" fill="none"/></svg>voluptatem accusantium</li><li><svg width="13" height="13" viewBox="0 0 14 14"><circle cx="7" cy="7" r="7" fill="#0a7ad6"/><path d="M4 7l2 2 4-4" stroke="#fff" stroke-width="1.8" fill="none"/></svg>doloremque laudantium,</li><li><svg width="13" height="13" viewBox="0 0 14 14"><circle cx="7" cy="7" r="7" fill="#0a7ad6"/><path d="M4 7l2 2 4-4" stroke="#fff" stroke-width="1.8" fill="none"/></svg>totam rem aperiam, eaque</li></ul>
    <div class="btn-line">START NOW</div>
  </div>

  <div class="plan pro" style="left:357px">
    <svg class="hex" width="66" height="74" viewBox="0 0 66 74"><path d="M33 0l33 18.5v37L33 74 0 55.5v-37z" fill="#fff"/><rect x="20" y="24" width="26" height="8" rx="1" stroke="#0a7ad6" stroke-width="2" fill="none"/><rect x="20" y="36" width="26" height="8" rx="1" stroke="#0a7ad6" stroke-width="2" fill="none"/><path d="M33 44v6M24 50h18" stroke="#0a7ad6" stroke-width="2"/></svg>
    <h3>Pro Plan</h3><div class="price">$ <b>15</b> .00/mo</div><div class="setup">Free Instant Setup</div>
    <ul><li><svg width="13" height="13" viewBox="0 0 14 14"><circle cx="7" cy="7" r="7" fill="#fff"/><path d="M4 7l2 2 4-4" stroke="#0a7ad6" stroke-width="1.8" fill="none"/></svg>Sed ut perspiciatis unde</li><li><svg width="13" height="13" viewBox="0 0 14 14"><circle cx="7" cy="7" r="7" fill="#fff"/><path d="M4 7l2 2 4-4" stroke="#0a7ad6" stroke-width="1.8" fill="none"/></svg>omnis iste natus error sit</li><li><svg width="13" height="13" viewBox="0 0 14 14"><circle cx="7" cy="7" r="7" fill="#fff"/><path d="M4 7l2 2 4-4" stroke="#0a7ad6" stroke-width="1.8" fill="none"/></svg>voluptatem accusantium</li><li><svg width="13" height="13" viewBox="0 0 14 14"><circle cx="7" cy="7" r="7" fill="#fff"/><path d="M4 7l2 2 4-4" stroke="#0a7ad6" stroke-width="1.8" fill="none"/></svg>doloremque laudantium,</li><li><svg width="13" height="13" viewBox="0 0 14 14"><circle cx="7" cy="7" r="7" fill="#fff"/><path d="M4 7l2 2 4-4" stroke="#0a7ad6" stroke-width="1.8" fill="none"/></svg>totam rem aperiam, eaque</li></ul>
    <div class="btn-line">START NOW</div>
  </div>

  <div class="plan" style="left:614px">
    <svg class="hex" width="66" height="74" viewBox="0 0 66 74"><path d="M33 0l33 18.5v37L33 74 0 55.5v-37z" fill="#0a7ad6"/><rect x="20" y="20" width="26" height="30" rx="2" stroke="#fff" stroke-width="2" fill="none"/><path d="M20 30h26M20 40h26" stroke="#fff" stroke-width="2"/></svg>
    <h3>Business Plan</h3><div class="price">$ <b>15</b> .00/mo</div><div class="setup">Free Instant Setup</div>
    <ul><li><svg width="13" height="13" viewBox="0 0 14 14"><circle cx="7" cy="7" r="7" fill="#0a7ad6"/><path d="M4 7l2 2 4-4" stroke="#fff" stroke-width="1.8" fill="none"/></svg>Sed ut perspiciatis unde</li><li><svg width="13" height="13" viewBox="0 0 14 14"><circle cx="7" cy="7" r="7" fill="#0a7ad6"/><path d="M4 7l2 2 4-4" stroke="#fff" stroke-width="1.8" fill="none"/></svg>omnis iste natus error sit</li><li><svg width="13" height="13" viewBox="0 0 14 14"><circle cx="7" cy="7" r="7" fill="#0a7ad6"/><path d="M4 7l2 2 4-4" stroke="#fff" stroke-width="1.8" fill="none"/></svg>voluptatem accusantium</li><li><svg width="13" height="13" viewBox="0 0 14 14"><circle cx="7" cy="7" r="7" fill="#0a7ad6"/><path d="M4 7l2 2 4-4" stroke="#fff" stroke-width="1.8" fill="none"/></svg>doloremque laudantium,</li><li><svg width="13" height="13" viewBox="0 0 14 14"><circle cx="7" cy="7" r="7" fill="#0a7ad6"/><path d="M4 7l2 2 4-4" stroke="#fff" stroke-width="1.8" fill="none"/></svg>totam rem aperiam, eaque</li></ul>
    <div class="btn-line">START NOW</div>
  </div>

  <div class="plan" style="left:872px">
    <svg class="hex" width="66" height="74" viewBox="0 0 66 74"><path d="M33 0l33 18.5v37L33 74 0 55.5v-37z" fill="#0a7ad6"/><rect x="18" y="24" width="20" height="22" rx="1" stroke="#fff" stroke-width="2" fill="none"/><circle cx="42" cy="32" r="7" stroke="#fff" stroke-width="2" fill="none"/><path d="M18 31h20M18 38h20" stroke="#fff" stroke-width="2"/></svg>
    <h3>NimbaVault Plan</h3><div class="price">$ <b>15</b> .00/mo</div><div class="setup">Free Instant Setup</div>
    <ul><li><svg width="13" height="13" viewBox="0 0 14 14"><circle cx="7" cy="7" r="7" fill="#0a7ad6"/><path d="M4 7l2 2 4-4" stroke="#fff" stroke-width="1.8" fill="none"/></svg>Sed ut perspiciatis unde</li><li><svg width="13" height="13" viewBox="0 0 14 14"><circle cx="7" cy="7" r="7" fill="#0a7ad6"/><path d="M4 7l2 2 4-4" stroke="#fff" stroke-width="1.8" fill="none"/></svg>omnis iste natus error sit</li><li><svg width="13" height="13" viewBox="0 0 14 14"><circle cx="7" cy="7" r="7" fill="#0a7ad6"/><path d="M4 7l2 2 4-4" stroke="#fff" stroke-width="1.8" fill="none"/></svg>voluptatem accusantium</li><li><svg width="13" height="13" viewBox="0 0 14 14"><circle cx="7" cy="7" r="7" fill="#0a7ad6"/><path d="M4 7l2 2 4-4" stroke="#fff" stroke-width="1.8" fill="none"/></svg>doloremque laudantium,</li><li><svg width="13" height="13" viewBox="0 0 14 14"><circle cx="7" cy="7" r="7" fill="#0a7ad6"/><path d="M4 7l2 2 4-4" stroke="#fff" stroke-width="1.8" fill="none"/></svg>totam rem aperiam, eaque</li></ul>
    <div class="btn-line">START NOW</div>
  </div>
</section>

<section class="signup">
  <div class="signup-photo" role="img" aria-label="Rows of server racks in a data centre, blue tint"></div>
  <h2><b>SIGN UP NOW FOR FAST RELIABLE &amp;</b><br>SECURE WEBSITE HOSTING</h2>
  <div class="pill" style="left:402px;background:#fff;color:#0a7ad6">WEB HOSTING <svg width="15" height="15" viewBox="0 0 16 16"><circle cx="8" cy="8" r="8" fill="#0a7ad6"/><path d="M6.5 4.5L10 8l-3.5 3.5" stroke="#fff" stroke-width="2" fill="none"/></svg></div>
  <div class="pill" style="left:609px;border:2px solid #fff;color:#fff">GET STARTED <svg width="15" height="15" viewBox="0 0 16 16"><circle cx="8" cy="8" r="8" fill="#fff"/><path d="M6.5 4.5L10 8l-3.5 3.5" stroke="#0a7ad6" stroke-width="2" fill="none"/></svg></div>
</section>

<section class="why">
  <div class="why-photo" role="img" aria-label="Technician working on a laptop between server racks"></div>
  <h2><b>WHY</b> CHOOSE US?</h2>
  <p class="lead">Lorem ipsum dolor sit amet, consectetur adipiscing elit, sed do eiusmod tempor incididunt ut labore et dolore magna aliqua. Ut enim ad minim veniam, quis nostrud exercitation ullamco laboris pariatur.</p>
  <div class="feat" style="left:580px;top:267px"><div class="ic"><svg width="28" height="28" viewBox="0 0 40 40" fill="none" stroke="#0a7ad6" stroke-width="2"><path d="M11 16a6 6 0 0 1 2-11 8 8 0 0 1 14 2 5 5 0 0 1 2 9z"/><rect x="12" y="20" width="16" height="12" rx="1"/></svg></div><h4>Sed perspiciatis unde omnis</h4><p>Lorem ipsum dolor sit consectetur adipiscing elit, sed do</p></div>
  <div class="feat" style="left:845px;top:267px"><div class="ic"><svg width="28" height="28" viewBox="0 0 40 40" fill="none" stroke="#0a7ad6" stroke-width="2"><rect x="6" y="8" width="28" height="20" rx="2"/><path d="M14 34h12M20 28v6M12 16h16"/></svg></div><h4>Sed perspiciatis unde omnis</h4><p>Lorem ipsum dolor sit consectetur adipiscing elit, sed do</p></div>
  <div class="feat" style="left:580px;top:429px"><div class="ic"><svg width="28" height="28" viewBox="0 0 40 40" fill="none" stroke="#0a7ad6" stroke-width="2"><ellipse cx="20" cy="9" rx="10" ry="4"/><path d="M10 9v20c0 2 4.5 4 10 4s10-2 10-4V9M10 19c0 2 4.5 4 10 4s10-2 10-4"/></svg></div><h4>Sed perspiciatis unde omnis</h4><p>Lorem ipsum dolor sit consectetur adipiscing elit, sed do</p></div>
  <div class="feat" style="left:845px;top:429px"><div class="ic"><svg width="28" height="28" viewBox="0 0 40 40" fill="none" stroke="#0a7ad6" stroke-width="2"><rect x="10" y="6" width="20" height="28" rx="2"/><path d="M14 13h12M14 20h12M14 27h6"/></svg></div><h4>Sed perspiciatis unde omnis</h4><p>Lorem ipsum dolor sit consectetur adipiscing elit, sed do</p></div>
</section>

<section class="clients">
  <div class="h-title" style="top:45px"><b>WHAT OUR</b> CLIENTS SAY</div>
  <div class="quote" style="left:111px"><div class="avatar" role="img" aria-label="Portrait photo of client Delia Marsh"></div><p>Sed ut perspiciatis unde omnis iste natus error sit voluptatem accusantium doloremque laudantium, totam rem aperiam, eaque ipsa</p></div>
  <div class="quote" style="left:446px"><div class="avatar" role="img" aria-label="Portrait photo of client Irene Calder"></div><p>Sed ut perspiciatis unde omnis iste natus error sit voluptatem accusantium doloremque laudantium, totam rem aperiam, eaque ipsa</p></div>
  <div class="quote" style="left:781px"><div class="avatar" role="img" aria-label="Portrait photo of client Tomas Reyno"></div><p>Sed ut perspiciatis unde omnis iste natus error sit voluptatem accusantium doloremque laudantium, totam rem aperiam, eaque ipsa</p></div>
  <div class="who" style="left:111px">Delia Marsh, <small>Chairman Orvane</small><span class="stars">★★★★★</span></div>
  <div class="who" style="left:446px">Irene Calder, <small>Project Manager</small><span class="stars">★★★★★</span></div>
  <div class="who" style="left:781px">Tomas Reyno, <small>Chairman Orvane</small><span class="stars">★★★★★</span></div>
</section>

<footer>
  <h5 style="left:110px">Contact Us</h5>
  <h5 style="left:424px">Links</h5>
  <h5 style="left:711px">Subscribe for Updates</h5>

  <div class="fitem" style="top:110px"><svg width="11" height="14" viewBox="0 0 10 12"><path d="M5 0a4 4 0 0 0-4 4c0 3 4 8 4 8s4-5 4-8a4 4 0 0 0-4-4z" fill="#0a7ad6"/></svg><span style="width:220px">10 Lorem ipsum dolor sit amet, consectetur elit,</span></div>
  <div class="fitem" style="top:171px"><svg width="14" height="10" viewBox="0 0 12 9"><rect width="12" height="9" fill="#0a7ad6"/><path d="M0 0l6 5 6-5" stroke="#58595b" fill="none"/></svg>info@nimbavault.com</div>
  <div class="fitem" style="top:207px"><svg width="13" height="13" viewBox="0 0 12 12"><path d="M2.5 0l2 3-1.3 1.3a8 8 0 0 0 4.5 4.5L9 7.5l3 2-1.5 2.5C5 12 0 7 0 1.5z" fill="#0a7ad6"/></svg>555 014 2290</div>
  <div class="fitem" style="top:242px"><svg width="14" height="13" viewBox="0 0 14 13"><rect y="1" width="14" height="12" rx="1" fill="#0a7ad6"/></svg>+1 555 017 3384</div>

  <span class="flink" style="left:424px;top:108px">Home</span>
  <span class="flink" style="left:424px;top:135px">About Us</span>
  <span class="flink" style="left:424px;top:161px">Services</span>
  <span class="flink" style="left:424px;top:188px">Plan</span>
  <span class="flink" style="left:424px;top:215px">Blog</span>
  <span class="flink" style="left:521px;top:108px">Terms &amp; Condition</span>
  <span class="flink" style="left:521px;top:135px">Privacy Policy</span>
  <span class="flink" style="left:521px;top:161px">Support</span>
  <span class="flink" style="left:521px;top:188px">Imprint</span>
  <span class="flink" style="left:521px;top:215px">Contact</span>

  <div class="email">Emaill Address</div>
  <div class="submit">SUBMIT</div>
  <span class="flink" style="left:711px;top:181px;font-size:13px;font-weight:500">☑&nbsp; Yes, Please Contact me.</span>
  <i class="fsoc" style="left:711px"></i><i class="fsoc" style="left:754px"></i><i class="fsoc" style="left:797px"></i>

  <div class="divider"></div>
  <div class="copy">© 2021 NimbaVault &nbsp;|&nbsp; All Rights Reserved</div>
</footer>

</body>
</html>
```